Tutoring center for k-12 and adults. ( name: Birch Tutoring )

We will start a tutoring center mainly teaching international students English, math, test prep ( SAT,ACT) for K-12 and English conversation class and English grammar for adults. Our mission and description is well described in the attached file below.
Our center is located in Ann Arbor Michigan, and will provide highly qualified instructors.
Our motto is " school like a home and teacher like parents" and "Birch Tutoring is the passage to success" and "Learn to think" I want you to have these main themes as designing the website, and we already have a designed logo attached below in the file. As the name shows, greenish, fresh feeling, but academically informative design is strongly recommended.
I want to emphasize warm and caring atmosphere of our center with the images fitting to this concept.

Target Market(s)

international students (k-12) and adults for ESL classes / high school students both American and international students for test preps: ACT,SAT

Industry/Entity Type

Education

Coding

Number of Pages Required

3 page

Font styles to use
Serif
Sans Serif
Script

Requirements
Must have
• I think there are many options in my website to create different things, but at this point, I just want to make four headings on the top- Home, About us, Classes, Support.
• Home page includes mission statement, testimonial, brief introduction of Test prep classes (SAT,ACT), academic tutoring, and adults classes. Also logo and contact info should be located in the first page. As a second page (heading), classes need to be introduced. I wonder if I can insert Korean for Korean classes. In this section, I want to put class descriptions of each class. As a third heading, About us includes introduction of instructors with their educational background, and please make two more open spots for instructors because we will add more faculties later.
• As the last heading, Support is the section for Q &A and provide the address and map of the center. This part is optional if I go with 3 pages of website!
• It should be informative and simple, easy to find the necessary info.
• If I can update the info by semester or periodically by myself. If it's easy to aces to change and manage the info for me, it will be great.
Nice to have
• .
• If I can have an option to convert the language of the website from English to Korean or to Chinese, it will be very nice.
Should not have
• lesson fees

```html
<!DOCTYPE html>
<html lang="en">
<head>
<meta charset="utf-8">
<title>Birch Tutoring</title>
<link rel="stylesheet" href="https://fonts.googleapis.com/css2?family=Raleway:wght@400;500;600&family=Open+Sans:ital,wght@0,400;0,600;1,400&display=swap">
<style>
:root{
  --navy:#0b3a66;
  --blue:#1a5aa8;
  --blue-deep:#084a9a;
  --sky:#7ca4d6;
  --lime:#8dc03b;
  --lime-dark:#6fa62a;
  --ink:#2b2b2b;
  --muted:#8a8a8a;
  --footer:#efefef;
  --white:#ffffff;
}
*{box-sizing:border-box;margin:0;padding:0}
html,body{width:1200px;height:2195px;overflow:hidden;background:var(--white)}
body{position:relative;font-family:'Open Sans',sans-serif;color:var(--ink)}
.abs{position:absolute}
h1,h2,h3,h4{font-family:'Raleway',sans-serif;font-weight:400}

/* header */
.brand{left:0;width:1200px;top:62px;text-align:center;font-family:'Raleway',sans-serif;font-weight:600;font-size:30px;color:var(--navy);letter-spacing:1px}
.brand-dot{display:inline-block;width:52px;height:52px;border-radius:50%;background:var(--navy);vertical-align:middle;margin-right:14px}
.lang{left:975px;top:104px;width:89px;height:25px;border:1px solid #d6d6d6;border-radius:2px;font-size:11px;line-height:23px;padding-left:10px;color:#444}
.lang-flag{display:inline-block;width:15px;height:10px;background:var(--blue);vertical-align:-1px;margin-right:5px}
.search{left:844px;top:139px;width:221px;height:26px;border:1px solid #d6d6d6;border-radius:2px;background:#f7f7f7;font-size:10px;font-style:italic;color:#999;line-height:24px;padding-left:12px}
.search svg{position:absolute;right:8px;top:5px}

/* nav */
.nav{left:0;top:181px;width:1200px;height:53px;background:linear-gradient(#1b6cc4,#0a4a96);display:flex;padding-left:136px}
.nav a{color:var(--white);text-decoration:none;font-family:'Raleway',sans-serif;font-weight:500;font-size:16px;line-height:53px;padding:0 17px;border-right:1px solid rgba(255,255,255,.35)}
.nav a:last-child{border-right:none}

/* hero */
.hero{left:0;top:234px;width:1200px;height:484px;background:linear-gradient(120deg,#6d7a86 0%,#a9a49b 45%,#cfc3b2 70%,#4c4540 100%)}
.hero svg{position:absolute;left:0;top:0}
.hero-title{left:133px;top:156px;color:var(--white);font-family:'Raleway',sans-serif;font-size:38px;font-weight:500}
.hero-sub{left:133px;top:208px;color:var(--white);font-family:'Raleway',sans-serif;font-size:26px;font-weight:500}
.hero-text{left:133px;top:252px;width:380px;color:#e8eef5;font-size:12px;line-height:19px}
.dots{left:133px;top:306px;display:flex;gap:6px}
.dots span{width:13px;height:13px;border-radius:50%;background:rgba(255,255,255,.45)}
.dots span:first-child{background:var(--white)}

/* intro */
.mission-title{left:140px;top:787px;font-size:26px;color:var(--ink)}
.mission-text{left:141px;top:828px;width:292px;font-size:11.5px;line-height:20px;color:var(--muted)}
.mission-text p+p{margin-top:11px}
.btn{left:142px;top:1010px;width:107px;height:29px;border-radius:3px;background:linear-gradient(#8fb3df,#5d8bc6);color:var(--white);font-size:11.5px;text-align:center;line-height:29px}
.card-img{top:777px;width:282px;height:143px}
.card-title{top:931px;font-size:26px}
.card-text{top:964px;width:290px;font-size:11.5px;line-height:20px;color:var(--muted)}
.card-more{top:1029px;font-size:12px;font-weight:600}
.card-more i{display:inline-block;width:18px;height:18px;border-radius:50%;background:#e4e4e4;vertical-align:middle;margin-left:8px;position:relative}
.card-more i:after{content:"";position:absolute;left:5px;top:6px;width:5px;height:5px;border-top:1.5px solid #888;border-right:1.5px solid #888;transform:rotate(45deg)}

/* classes */
.classes{left:0;top:1122px;width:1200px;height:397px;background:linear-gradient(90deg,#3d4a55,#5f6467 45%,#4a4f55)}
.classes-title{left:0;width:1200px;top:38px;text-align:center;color:var(--white);font-size:32px}
.circle{top:89px;width:254px;height:254px;border-radius:50%;text-align:center;color:var(--white)}
.circle svg{display:block;margin:52px auto 0}
.circle h3{font-size:28px;margin-top:8px}
.circle p{font-size:10px;line-height:20px;width:190px;margin:4px auto 0;opacity:.9}

/* gallery + testimonials */
.gal-title{left:135px;top:1580px;font-size:29px;color:var(--lime)}
.gal{left:138px;top:1639px;width:444px;display:grid;grid-template-columns:repeat(3,144px);grid-auto-rows:91px;gap:7px 6px}
.test-title{left:615px;top:1580px;font-size:29px;color:var(--navy)}
.arrow{top:1589px;width:26px;height:26px;border-radius:50%;background:#e4e4e4}
.arrow:after{content:"";position:absolute;top:9px;width:7px;height:7px;border-top:1.5px solid #888;border-right:1.5px solid #888}
.arrow.prev:after{left:11px;transform:rotate(-135deg)}
.arrow.next:after{left:8px;transform:rotate(45deg)}
.testimonial{left:626px;top:1643px;width:434px}
.quote{position:relative;font-size:11px;line-height:24px;font-style:italic;color:#777;text-indent:25px}
.quote .open{position:absolute;left:0;top:-4px;font-family:Georgia,serif;font-size:40px;line-height:1;color:#bbb;font-style:normal;text-indent:0}
.quote .close{display:inline-block;height:0;line-height:0;vertical-align:top;margin-left:4px;font-family:Georgia,serif;font-size:40px;color:#bbb;font-style:normal;text-indent:0;position:relative;top:20px}
.quote-by{margin-top:6px;font-size:13px;color:var(--navy);font-family:'Raleway',sans-serif;font-weight:500;padding-left:3px}

/* footer */
.footer{left:0;top:1902px;width:1200px;height:293px;background:var(--footer)}
.fcol{top:50px}
.fcol h4{font-size:17px;color:#333;margin-bottom:10px}
.fcol li{list-style:none;font-size:12px;line-height:25px;color:#777}
.social{display:flex;gap:14px;margin-top:12px}
.social span{width:24px;height:24px;border-radius:50%;background:#bdbdbd}
.frule{left:151px;top:235px;width:934px;height:1px;background:#d8d8d8}
.copy{left:151px;top:257px;font-size:10.5px;color:#777}
</style>
</head>
<body>

<header>
  <div class="abs brand"><span class="brand-dot"></span>Birch Tutoring</div>
  <div class="abs lang"><span class="lang-flag"></span>English ▾</div>
  <div class="abs search">Search here
    <svg width="14" height="14" viewBox="0 0 14 14"><circle cx="6" cy="6" r="4.5" fill="none" stroke="#999" stroke-width="1.5"/><line x1="9.3" y1="9.3" x2="13" y2="13" stroke="#999" stroke-width="1.5"/></svg>
  </div>
</header>

<nav class="abs nav">
  <a>Home</a><a>Mission Statement</a><a>Classes Instructors</a><a>Location</a><a>Testimonials</a><a>Academic Pictures</a><a>Contact us.</a>
</nav>

<section class="abs hero" role="img" aria-label="Photo of a student reading a large open book">
  <svg width="1200" height="484" viewBox="0 0 1200 484">
    <polygon points="0,0 476,0 607,285 329,484 0,484" fill="#0b3f73" opacity=".82"/>
    <polygon points="329,484 607,285 702,484" fill="#6ea52a"/>
    <polygon points="476,484 607,285 702,484" fill="#8dc03b"/>
  </svg>
  <h1 class="abs hero-title">SCHOOL LIKE A HOME</h1>
  <h2 class="abs hero-sub">AND TEACHER LIKE PARENTS</h2>
  <p class="abs hero-text">Vivamus porttitor purus nisi eleifend libero a tempus libero lectus feugiat felis Morbi diam mauris viverra in gravida eu</p>
  <div class="abs dots"><span></span><span></span><span></span><span></span></div>
</section>

<section>
  <h2 class="abs mission-title">Our Mission</h2>
  <div class="abs mission-text">
    <p>We are highly motivated to stimulate student's ability to get the best of their ability in academic field. Our teachers are experienced in teaching K-12 students through adult students.</p>
    <p>Especially, they will help students to improve student's academic qualifications and performance and to enhance possibilities for admission into colleges and universities in the United States.</p>
  </div>
  <div class="abs btn">READ MORE</div>

  <div class="abs card-img" style="left:473px;background:linear-gradient(90deg,#2a2a2a,#9a9a9a 50%,#3a3a3a)" role="img" aria-label="Black and white photo of library bookshelves"></div>
  <h3 class="abs card-title" style="left:477px;color:var(--blue)">About Us</h3>
  <p class="abs card-text" style="left:477px">We are located in Ann Arbor, one of the hub cities of American education. We provide a highly qualified and selective education to lead our students</p>
  <div class="abs card-more" style="left:477px;color:var(--navy)">Read More<i></i></div>

  <div class="abs card-img" style="left:784px;background:linear-gradient(#c9ccd2,#e7e4de 60%,#3e4756)" role="img" aria-label="Photo of an open book"></div>
  <h3 class="abs card-title" style="left:783px;color:var(--lime)">Location</h3>
  <p class="abs card-text" style="left:783px">Maecenas aliquet velit vel turpis Mauris neque metus malesuada nec ultricies sit amet porttitor mattis enim in massa libero interdum nec interdum</p>
  <div class="abs card-more" style="left:783px;color:var(--lime-dark)">Read More<i></i></div>
</section>

<section class="abs classes" role="img" aria-label="Photo of students studying together at a table">
  <h2 class="abs classes-title">Classes Instructors</h2>

  <div class="abs circle" style="left:147px;background:var(--lime)">
    <svg width="70" height="46" viewBox="0 0 70 46"><rect x="2" y="2" width="66" height="42" fill="none" stroke="#fff" stroke-width="3"/><line x1="35" y1="2" x2="35" y2="44" stroke="#fff" stroke-width="3"/><line x1="2" y1="23" x2="68" y2="23" stroke="#fff" stroke-width="3"/></svg>
    <h3>English</h3>
    <p>Class aptent taciti sociosqu ad litora torquent per conubia no</p>
  </div>
  <div class="abs circle" style="left:363px;background:var(--navy)">
    <svg width="56" height="50" viewBox="0 0 56 50" style="margin-top:46px"><path d="M28 3 L6 40 M28 3 L50 40" stroke="#fff" stroke-width="2.5" fill="none"/><ellipse cx="28" cy="40" rx="22" ry="7" fill="none" stroke="#fff" stroke-width="2.5"/><line x1="28" y1="3" x2="28" y2="40" stroke="#fff" stroke-width="1.5" stroke-dasharray="3 3"/></svg>
    <h3>Math</h3>
    <p>Class aptent taciti sociosqu ad litora torquent per conubia no</p>
  </div>
  <div class="abs circle" style="left:580px;background:var(--sky)">
    <svg width="48" height="56" viewBox="0 0 48 56" style="margin-top:44px"><rect x="3" y="3" width="34" height="48" rx="3" fill="none" stroke="#fff" stroke-width="2.5"/><g stroke="#fff" stroke-width="2"><line x1="14" y1="14" x2="30" y2="14"/><line x1="14" y1="23" x2="30" y2="23"/><line x1="14" y1="32" x2="26" y2="32"/><line x1="14" y1="41" x2="22" y2="41"/></g><g fill="#fff"><circle cx="9" cy="14" r="1.6"/><circle cx="9" cy="23" r="1.6"/><circle cx="9" cy="32" r="1.6"/><circle cx="9" cy="41" r="1.6"/></g><line x1="44" y1="26" x2="30" y2="50" stroke="#fff" stroke-width="3"/></svg>
    <h3>Test Prep</h3>
    <p>Class aptent taciti sociosqu ad litora torquent per conubia no</p>
  </div>
  <div class="abs circle" style="left:798px;background:var(--blue-deep)">
    <svg width="62" height="56" viewBox="0 0 62 56" style="margin-top:44px"><text x="4" y="20" fill="#fff" font-family="Georgia,serif" font-weight="bold" font-size="22">ABC</text><path d="M10 36 L24 50 L56 22" stroke="#fff" stroke-width="6" fill="none"/></svg>
    <h3>Grammer</h3>
    <p>Class aptent taciti sociosqu ad litora torquent per conubia no</p>
  </div>
</section>

<section>
  <h2 class="abs gal-title">Academic Pictures</h2>
  <div class="abs gal">
    <div style="background:linear-gradient(135deg,#5b7fa8,#d7b592)" role="img" aria-label="Photo of a smiling student holding books"></div>
    <div style="background:linear-gradient(135deg,#c9b9a6,#7a6656)" role="img" aria-label="Photo of a teacher helping children"></div>
    <div style="background:linear-gradient(135deg,#e9ecef,#8a9bb0)" role="img" aria-label="Photo of a classroom with a whiteboard"></div>
    <div style="background:linear-gradient(135deg,#415a7a,#b08a6e)" role="img" aria-label="Photo of a student in a classroom"></div>
    <div style="background:linear-gradient(135deg,#b5a48f,#7c8f5c)" role="img" aria-label="Photo of students working at a table"></div>
    <div style="background:linear-gradient(135deg,#d6c6b4,#8d6e57)" role="img" aria-label="Photo of children studying together"></div>
  </div>

  <h2 class="abs test-title">Testimonials</h2>
  <div class="abs arrow prev" style="left:992px"></div>
  <div class="abs arrow next" style="left:1024px"></div>
  <div class="abs testimonial">
    <blockquote class="quote"><span class="open">&ldquo;</span>Hana Lim is my great tutor. I have learned English from scratch for about two years from her. She is the best if you want to learn English. Meanwhile my English improved amazingly. She won't give you the fish caught by she will teach you how to catch the fish. Surely she will make your basics of English very solid, so you are absolutely able to use English fully little by little. I believe, if you meet her, it would be a blessing for you.<span class="close">&rdquo;</span></blockquote>
    <div class="quote-by">By Student Name</div>
  </div>
</section>

<footer class="abs footer">
  <div class="abs fcol" style="left:151px"><h4>Quick Links</h4><ul><li>Home</li><li>Mission statement</li><li>Classes Instructors</li><li>Location</li></ul></div>
  <div class="abs fcol" style="left:325px"><h4>Resources</h4><ul><li>Testimonials</li><li>Academic Pictures</li><li>Contact us.</li></ul></div>
  <div class="abs fcol" style="left:500px"><h4>Support</h4><ul><li>Join Us Now</li><li>Testimonials</li><li>Term of Use</li></ul></div>
  <div class="abs fcol" style="left:656px"><h4>Contact Info</h4><ul><li>214 Maple Grove Road Suite 3B</li><li>Ann Arbor, MI 48104</li><li>Phone: (555) 310-4872</li><li>Email: hello@birchtutoring.example</li></ul></div>
  <div class="abs fcol" style="left:901px"><h4>Stay in touch</h4><ul><li style="font-size:10.5px">Connect with us on social sites.</li></ul>
    <div class="social"><span></span><span></span><span></span><span></span></div>
  </div>
  <div class="abs frule"></div>
  <div class="abs copy">© 2015 Company Name &nbsp;All right reserved &nbsp;Term of Use</div>
</footer>

</body>
</html>
```